PixelMarrow Inc. Website & iPhone Apps Landing Pages

We need a web site design for our company. We develop software and do various consultant projects for our clients. Our products focus on the mobile platform, mainly the iPhone (business, games, social, etc.). We want to communicate that our software is simple and good as candy. The web pages should be fun to look at not loosing seriousness and credibility. Web 2.0 style and 960 grid system a must. We are opened to any overall site colour scheme suggestions (look at the sites we like below).

Must haves:
- Our logo should be seen on the site and look great on it :-) (preview attached below)
- Main home page and app landing page.
- Section links/tabs on the home page (home,apps,support,blog,contact,about)
- No text in images
- Style sheet

Looks we like:
- http://k7q3vxp9lrtwz.examplecdn.net/441_Site_Mock/final_large.jpg
- http://k7q3vxp9lrtwz.examplecdn.net/Deluxe_71_Drawn_Phone_Landing_Page/final.jpg
- http://grenmoor.com/
- http://lumbrel.ca/
- http://fairtwig.com/

Industry/Entity Type

Business

Requirements
Must have
• - Company logo should look great on pages.
• - Main home page and app landing page.
• - Section links/tabs on the home page (home,apps,support,blog,contact,about)
• - Web 2.0 style.
• - 960 grid system (12 col, 16 col).
• - Sliced ann optmized
• - Exported in all major formats (psd,ai,eps,png,jpeg,etc)
• - Style sheet
Should not have
• - Text in images

```html
<!DOCTYPE html>
<html lang="en">
<head>
<meta charset="utf-8">
<title>PixelMarrow — Home</title>
<link rel="stylesheet" href="https://fonts.googleapis.com/css2?family=Arimo:wght@400;700&family=Oswald:wght@500&display=swap">
<style>
:root{
  --page-bg:#333132;
  --page-bg-dark:#262425;
  --card:#ffffff;
  --accent:#e2474b;
  --accent-dark:#c8252a;
  --text:#444444;
  --text-dark:#111111;
  --footer-text:#e8e8e8;
  --footer-rule:#5a5859;
  --muted:#8c8a8b;
  --green-light:#d6f0a0;
  --green:#7cc23a;
  --green-dark:#4e9a1e;
  --btn-top:#fff6a8;
  --btn-bottom:#f7cf2a;
  --arrow:#e0531b;
}
*{margin:0;padding:0;box-sizing:border-box}
html,body{width:830px;height:1200px;overflow:hidden}
body{position:relative;background:var(--page-bg);font-family:"Arimo",Arial,sans-serif;color:var(--text)}
.abs{position:absolute}

.card{position:absolute;left:28px;top:27px;width:778px;height:824px;background:var(--card);border-radius:6px}

.logo{position:absolute;left:53px;top:50px;font-size:31px;font-weight:700;color:var(--accent-dark);letter-spacing:-0.5px;line-height:1}

.nav{position:absolute;top:42px;left:0;width:830px;height:60px;list-style:none}
.nav li{position:absolute;top:0;text-align:center;font-size:15px;color:#555}
.nav li svg{display:block;margin:0 auto 6px;width:28px;height:28px}
.nav li.current{color:var(--accent)}
.nav li.current span{border-bottom:2px solid var(--accent);padding-bottom:1px}

.hero{position:absolute;left:50px;top:112px;width:731px;height:364px;border-radius:5px;
  background:radial-gradient(ellipse at 20% 35%,#f4fbd8 0%,var(--green-light) 25%,var(--green) 65%,var(--green-dark) 100%)}
.hero-shadow{position:absolute;left:80px;top:478px;width:670px;height:14px;border-radius:50%;background:radial-gradient(ellipse,rgba(0,0,0,.14),rgba(0,0,0,0) 70%)}
.cta{position:absolute;left:552px;top:400px;width:215px;height:54px;border-radius:10px;
  background:linear-gradient(var(--btn-top),var(--btn-bottom));border:2px solid #fff2a0;
  box-shadow:0 2px 4px rgba(0,0,0,.25);font-family:"Oswald","Arial Narrow",sans-serif;font-size:23px;font-weight:500;color:#1a1a1a;
  line-height:50px;padding-left:18px;white-space:nowrap}
.cta svg{position:absolute;right:11px;top:-2px}

.col-rule{position:absolute;top:516px;width:1px;height:296px;background:#e2e2e2}
.col-head{position:absolute;font-size:22px;font-weight:700;color:var(--accent);letter-spacing:-0.5px;line-height:1}
.col-icon{position:absolute;width:34px;height:34px;border-radius:4px}

.features{position:absolute;left:50px;top:565px;list-style:none}
.features li{position:relative;width:200px;height:54px;padding-left:22px;font-size:10.5px;line-height:14px;color:var(--text)}
.features li svg{position:absolute;left:0;top:5px}

.video{position:absolute;left:269px;top:576px;width:276px;height:194px;background:linear-gradient(#2a2a2a,#000 75%)}
.play{position:absolute;left:98px;top:74px;width:79px;height:24px;border-radius:12px;border:1.5px solid #777;
  background:linear-gradient(#6c6c6c,#3a3a3a);color:#ddd;font-size:8.5px;line-height:21px;padding-left:13px}
.play svg{position:absolute;right:-1px;top:-1px}
.controls{position:absolute;left:0;bottom:0;width:276px;height:16px;background:linear-gradient(#3b4a55,#1b242b)}
.controls .track{position:absolute;left:18px;top:5px;width:152px;height:6px;border-radius:3px;background:#0a0a0a}
.controls .time{position:absolute;left:167px;top:3px;font-size:7px;color:#9ac4e0}
.controls .vol{position:absolute;left:238px;top:6px;width:26px;height:4px;border-radius:2px;background:#ccc}

.quote{position:absolute;left:576px;top:576px;width:196px;font-size:10.5px;line-height:19.5px;color:var(--text)}
.quote .who{color:var(--text-dark);font-weight:700;font-size:10.5px}

.foot-col{position:absolute;top:877px}
.foot-col h3{font-size:16px;font-weight:700;color:#f2f2f2;text-shadow:1px 1px 1px #000;letter-spacing:-0.3px;line-height:1;padding-bottom:7px;border-bottom:1px solid var(--footer-rule);margin-bottom:9px}
.foot-col p{font-size:10.5px;line-height:13.7px;color:var(--footer-text)}
.foot-col .gap{margin-top:7px}
.blog-item{margin-bottom:13px;padding-left:3px}

.bottom-bar{position:absolute;left:0;top:1105px;width:830px;height:95px;border-top:1px solid #4a4849;background:linear-gradient(var(--page-bg-dark),#2c2a2b)}
.bottom-nav{position:absolute;left:38px;top:20px;font-size:10.5px;font-weight:700;color:#fff}
.bottom-nav span{color:#ddd;font-weight:400;margin:0 8px}
.bottom-logo{position:absolute;right:33px;top:13px;font-size:18px;color:var(--muted);line-height:1}
.copyright{position:absolute;right:33px;top:38px;font-size:9px;color:var(--muted)}
</style>
</head>
<body>

<div class="card"></div>

<div class="logo">pixelmarrow</div>

<ul class="nav">
  <li class="current" style="left:414px;width:50px">
    <svg viewBox="0 0 28 28"><path d="M3 14L14 4l11 10h-3v10H6V14z" fill="#5aa0d8" stroke="#2f6fa8"/><circle cx="14" cy="16" r="4" fill="#fff"/></svg>
    <span>home</span>
  </li>
  <li style="left:472px;width:46px">
    <svg viewBox="0 0 28 28"><g fill="#d94a8c"><circle cx="9" cy="9" r="3"/><circle cx="19" cy="9" r="3" fill="#4aa0e0"/><circle cx="9" cy="19" r="3" fill="#f0b030"/><circle cx="19" cy="19" r="3" fill="#6cc040"/></g></svg>
    <span>apps</span>
  </li>
  <li style="left:530px;width:60px">
    <svg viewBox="0 0 28 28"><circle cx="14" cy="14" r="11" fill="none" stroke="#d33" stroke-width="3"/><text x="14" y="19" font-size="14" font-weight="700" text-anchor="middle" fill="#333" font-family="Arimo,sans-serif">?</text></svg>
    <span>support</span>
  </li>
  <li style="left:603px;width:42px">
    <svg viewBox="0 0 28 28"><rect x="3" y="3" width="22" height="22" rx="4" fill="#f3902a"/><circle cx="9" cy="19" r="2" fill="#fff"/><path d="M8 12a8 8 0 0 1 8 8M8 7a13 13 0 0 1 13 13" stroke="#fff" stroke-width="2" fill="none"/></svg>
    <span>blog</span>
  </li>
  <li style="left:656px;width:56px">
    <svg viewBox="0 0 28 28"><rect x="3" y="7" width="22" height="15" fill="#e8eef4" stroke="#9ab"/><path d="M3 7l11 9 11-9" fill="none" stroke="#9ab"/></svg>
    <span>contact</span>
  </li>
  <li style="left:727px;width:46px">
    <svg viewBox="0 0 28 28"><circle cx="14" cy="10" r="6" fill="#6cb82c"/><path d="M4 25c0-7 4-9 10-9s10 2 10 9z" fill="#6cb82c"/></svg>
    <span>about</span>
  </li>
</ul>

<div class="hero" role="img" aria-label="Three smartphones showing app screens over a green bokeh background"></div>
<div class="hero-shadow"></div>
<div class="cta">DOWNLOAD NOW
  <svg width="24" height="42" viewBox="0 0 24 42"><path d="M7 0h10v24h7L12 42 0 24h7z" fill="var(--arrow)"/></svg>
</div>

<div class="col-rule" style="left:260px"></div>
<div class="col-rule" style="left:555px"></div>

<div class="col-icon" role="img" aria-label="Notepad and pen icon" style="left:51px;top:520px;background:#dde6ef"></div>
<div class="col-head" style="left:89px;top:527px">Features</div>

<ul class="features">
  <li><svg width="14" height="14" viewBox="0 0 14 14"><path d="M1 8l4 4 8-11" fill="none" stroke="#777" stroke-width="1.6"/></svg>Lorem ipsum dolor sit amet, con-sectetur adipiscing elit. Nam eget magna non.</li>
  <li><svg width="14" height="14" viewBox="0 0 14 14"><path d="M1 8l4 4 8-11" fill="none" stroke="#777" stroke-width="1.6"/></svg>Lorem ipsum dolor sit amet, con-sectetur adipiscing elit. Nam eget magna non.</li>
  <li><svg width="14" height="14" viewBox="0 0 14 14"><path d="M1 8l4 4 8-11" fill="none" stroke="#777" stroke-width="1.6"/></svg>Lorem ipsum dolor sit amet, con-sectetur adipiscing elit. Nam eget magna non.</li>
  <li><svg width="14" height="14" viewBox="0 0 14 14"><path d="M1 8l4 4 8-11" fill="none" stroke="#777" stroke-width="1.6"/></svg>Lorem ipsum dolor sit amet, con-sectetur adipiscing elit. Nam eget magna non.</li>
</ul>

<div class="col-icon" role="img" aria-label="Person presenting at a desk icon" style="left:275px;top:521px;width:44px;background:#e3ecf4"></div>
<div class="col-head" style="left:325px;top:530px">Check out the DEMO</div>

<div class="video">
  <div class="play">Show me
    <svg width="24" height="24" viewBox="0 0 24 24"><circle cx="12" cy="12" r="11" fill="#444" stroke="#999"/><path d="M9 7l8 5-8 5z" fill="#ccc"/></svg>
  </div>
  <div class="controls">
    <svg class="abs" style="left:5px;top:3px" width="10" height="10" viewBox="0 0 10 10"><path d="M2 1l7 4-7 4z" fill="#9ab"/></svg>
    <div class="track"></div>
    <div class="time">00:27 / 02:04</div>
    <div class="vol"></div>
  </div>
</div>

<div class="col-icon" role="img" aria-label="Person with speech bubble icon" style="left:571px;top:520px;background:#e3eef6"></div>
<div class="col-head" style="left:616px;top:527px">Testimonials</div>

<div class="quote">
  "We had been waiting for an easy to use application like PixelMarrow that would combine collaboration func-tions (similar to those in popular social networking sites), security that would enable us to protect assets and access, and robust file sharing that was reliable and would accom-modate the size and variety of files we work with."
  <div class="who">Marla Tennick</div>
  <div class="who">CEO, Company</div>
</div>

<div class="foot-col" style="left:38px;width:201px">
  <h3>About PixelMarrow</h3>
  <p>Lorem ipsum dolor sit amet, consectetur adipiscing elit. Nam eget magna non. Lorem ipsum dolor sit amet, consectetur adipiscing elit. Nam eget magna non. Lorem ipsum dolor sit amet, consectetur adipiscing elit.</p>
  <p class="gap">Nam eget magna non.<br>Lorem ipsum dolor sit amet, consectetur adipiscing elit. Nam eget magna non.</p>
</div>

<div class="foot-col" style="left:280px;width:259px">
  <h3>Support</h3>
  <p>Lorem ipsum dolor sit amet, consectetur adipiscing elit. Nam eget magna non. Lorem ipsum dolor sit amet, consectetur adipiscing elit. Nam eget magna non. Lorem ipsum dolor sit amet, consectetur adip-iscing elit. Lorem ipsum dolor sit amet, consectetur adipiscing elit. Nam eget magna non. Lorem ipsum dolor sit amet, consectetur adipiscing elit. Nam eget magna non. Lorem ipsum dolor sit amet, con-sectetur adipiscing elit.</p>
</div>

<div class="foot-col" style="left:572px;width:224px">
  <h3>Our Blog</h3>
  <p class="blog-item">Lorem ipsum dolor sit amet, consectetur adipiscing elit. Nam eget magna non.<br>Oct 25, 2010</p>
  <p class="blog-item">Lorem ipsum dolor sit amet, consectetur adipiscing elit. Nam eget magna non.<br>Oct 25, 2010</p>
  <p class="blog-item">Lorem ipsum dolor sit amet, consectetur adipiscing elit. Nam eget magna non.<br>Oct 25, 2010</p>
</div>

<div class="bottom-bar">
  <div class="bottom-nav">home<span>/</span>apps<span>/</span>support<span>/</span>blog<span>/</span>contact<span>/</span>about</div>
  <div class="bottom-logo">pixelmarrow</div>
  <div class="copyright">copyright©2010. All rights reserver.</div>
</div>

</body>
</html>
```